Logo, Web and Mobile Designs for enterprise social media platform

All the details are in the attached document, please start reading the scope document first which explains what is this project about and the details about the needed deliverables, after that please read the UI_Requirements document which will detail what is expected regarding the coded web version since this is a coded contest, it is very important that you meet the UI requirements or suggest something else but we will need to agree first before working on the coded version

Good Luck

Target Market(s)

Enterprise Social Media

Industry/Entity Type

Media

Coding

Coded - Design and coding required

Number of Pages Required

5+ page

Font styles to use
Sans Serif

Requirements
Must have
• All the must haves are listed in the scope document so please check before you start

```html
<!DOCTYPE html>
<html lang="en">
<head>
<meta charset="utf-8">
<title>Teamora – Feed</title>
<link href="https://fonts.googleapis.com/css2?family=Roboto:ital,wght@0,300;0,400;0,500;0,700;1,400&display=swap" rel="stylesheet">
<style>
:root{
  --bg:#eceef0;
  --card:#ffffff;
  --line:#e1e4e7;
  --text:#555b61;
  --muted:#8a9096;
  --brand:#2a7fb8;
  --name:#2f5b9b;
  --accent:#2290cf;
  --orange:#f2a21a;
  --footer:#2587b5;
  --fb:#3b5a96;
  --tw:#1fb3e8;
  --gp:#dd4b39;
}
*{box-sizing:border-box;margin:0;padding:0}
html,body{width:749px;height:1200px;overflow:hidden}
body{background:var(--bg);font-family:'Roboto',sans-serif;color:var(--text);position:relative}
.topbar{position:absolute;left:0;top:0;width:749px;height:44px;background:#fafafa;border-bottom:1px solid var(--line)}
.menu-btn{position:absolute;left:62px;top:17px;width:12px}
.menu-btn span{display:block;height:2px;background:#888;margin-bottom:2px}
.topbar-sep{position:absolute;top:0;width:1px;height:44px;background:var(--line)}
.brand{position:absolute;left:106px;top:10px;display:flex;align-items:center;gap:6px}
.brand-dot{width:24px;height:24px;border-radius:50%;background:var(--orange)}
.brand-name{font-size:19px;font-weight:500;color:var(--brand)}
.user{position:absolute;left:465px;top:12px;display:flex;align-items:center;gap:7px;font-size:11px;color:#444}
.avatar{border-radius:50%;background:linear-gradient(135deg,#8a6c55,#3e3029)}
.caret{width:0;height:0;border-left:4px solid transparent;border-right:4px solid transparent;border-top:5px solid #666;margin-left:5px}
.tool{position:absolute;top:13px}
.badge{position:absolute;top:-4px;right:-8px;width:11px;height:11px;border-radius:50%;font-size:7px;color:#fff;text-align:center;line-height:11px}
.card{position:absolute;background:var(--card);border:1px solid var(--line)}
.status{left:62px;top:61px;width:425px;height:228px}
.status h2{font-size:14px;font-weight:400;color:var(--name);position:absolute;left:14px;top:12px}
.status-box{position:absolute;left:14px;top:34px;width:395px;height:128px;border:1px solid var(--line)}
.status-box::after{content:"";position:absolute;left:28px;bottom:-9px;width:14px;height:14px;background:#fff;border-right:1px solid var(--line);border-bottom:1px solid var(--line);transform:rotate(45deg)}
.post-types{position:absolute;left:0;bottom:0;display:flex;height:46px}
.post-type{width:53px;text-align:center;font-size:10px;color:#555;border-right:1px solid var(--line);padding-top:7px}
.post-type svg{display:block;margin:0 auto 4px}
.post{left:62px;width:425px;height:250px}
.post .avatar{position:absolute;left:15px;top:10px;width:31px;height:31px}
.post .author{position:absolute;left:56px;top:13px;font-size:10px;color:var(--name)}
.post .date{position:absolute;left:56px;top:28px;font-size:7.5px;color:#777}
.post .globe{position:absolute;left:131px;top:16px;width:5px;height:5px;border-radius:50%;background:#bbb}
.post .media{position:absolute;left:15px;top:51px;width:393px;height:103px}
.post h3{position:absolute;left:14px;top:165px;font-size:10.5px;font-weight:400;color:#555}
.post p{position:absolute;left:15px;top:184px;width:370px;font-size:7px;line-height:12px;color:#666}
.actions{position:absolute;left:0;bottom:0;width:100%;height:18px;background:#f3f4f5;border-top:1px solid var(--line);display:flex;gap:16px;padding-left:26px;align-items:center;font-size:6.5px;color:#555}
.actions span::before{content:"";display:inline-block;width:5px;height:5px;background:#888;border-radius:1px;margin-right:5px;vertical-align:-1px}
.widget{left:512px;width:175px}
.widget-head{height:20px;border-bottom:1px solid var(--line);background:#f7f8f9;font-size:8px;color:#555;padding:6px 7px;position:relative}
.widget-head::after{content:"";position:absolute;right:8px;top:7px;width:4px;height:4px;border-right:1px solid #aaa;border-top:1px solid #aaa;transform:rotate(45deg)}
.item{position:relative;height:61px;border-bottom:1px solid var(--line)}
.item:last-child{border-bottom:0}
.thumb{position:absolute;left:9px;top:12px;width:46px;height:36px}
.person{position:absolute;left:9px;top:10px;width:46px;height:46px;border-radius:50%}
.item .txt{position:absolute;left:63px;top:9px;width:108px;font-size:6.5px;font-style:italic;line-height:12px;color:#555}
.item .meta{position:absolute;left:63px;top:36px;font-size:7px;color:var(--accent);display:flex;gap:22px}
.stars{color:var(--orange);letter-spacing:-0.5px;font-size:7px}
.stars i{color:#ccc;font-style:normal}
.grid{display:grid;grid-template-columns:repeat(3,52px);gap:2px;padding:7px}
.grid div{height:52px}
.socials{position:absolute;left:518px;top:724px;display:flex;gap:6px}
.social{width:50px;height:50px;color:#fff;font-size:8px;text-align:center;line-height:10px;padding-top:8px}
.social i{display:block;width:10px;height:10px;border-radius:50%;background:#fff;margin:0 auto 6px}
.fb{background:var(--fb)}.tw{background:var(--tw)}.gp{background:var(--gp)}
.footer{position:absolute;left:0;top:1108px;width:749px;height:92px;background:var(--footer);color:#fff;text-align:center}
.footer-icons{display:flex;gap:8px;justify-content:center;padding-top:16px}
.footer-icons span{width:15px;height:15px;border-radius:3px;background:#fff}
.footer nav{font-size:9px;margin-top:10px;color:#e8f3f9}
.footer nav b{font-weight:400;margin:0 6px}
.copyright{font-size:8.5px;margin-top:10px}
</style>
</head>
<body>
<header class="topbar">
  <div class="menu-btn"><span></span><span></span><span></span></div>
  <div class="topbar-sep" style="left:92px"></div>
  <div class="brand"><div class="brand-dot"></div><div class="brand-name">Teamora</div></div>
  <div class="user"><div class="avatar" style="width:22px;height:22px" role="img" aria-label="User profile photo"></div>Mark Ellison<div class="caret"></div></div>
  <div class="topbar-sep" style="left:570px"></div>
  <div class="tool" style="left:590px"><svg width="12" height="12"><rect x="0" y="1" width="12" height="2" fill="#666"/><rect x="0" y="5" width="8" height="2" fill="#666"/><rect x="0" y="9" width="10" height="2" fill="#666"/></svg><span class="badge" style="background:var(--orange)">8</span></div>
  <div class="topbar-sep" style="left:617px"></div>
  <div class="tool" style="left:630px"><svg width="13" height="13"><circle cx="5.5" cy="5.5" r="4.2" stroke="#666" stroke-width="1.6" fill="none"/><line x1="8.5" y1="8.5" x2="12" y2="12" stroke="#666" stroke-width="1.8"/></svg></div>
  <div class="topbar-sep" style="left:655px"></div>
  <div class="tool" style="left:669px"><svg width="12" height="13"><path d="M6 1c3 0 4 2 4 5v3l1.5 1.5h-11L2 9V6c0-3 1-5 4-5z" fill="#666"/><circle cx="6" cy="12" r="1.3" fill="#666"/></svg><span class="badge" style="background:var(--accent)">8</span></div>
  <div class="topbar-sep" style="left:697px"></div>
</header>

<section class="card status">
  <h2>Status</h2>
  <div class="status-box"></div>
  <div class="post-types">
    <div class="post-type"><svg width="12" height="12"><path d="M2 10l1-3 6-6 2 2-6 6z" fill="#666"/></svg>Text</div>
    <div class="post-type"><svg width="14" height="12"><rect x="1" y="2" width="12" height="9" rx="1" fill="none" stroke="#666" stroke-width="1.3"/><circle cx="7" cy="6.5" r="2.3" fill="#666"/></svg>Photo</div>
    <div class="post-type"><svg width="14" height="12"><rect x="1" y="3" width="8" height="7" fill="#666"/><path d="M9 6l4-3v7l-4-3z" fill="#666"/></svg>Video</div>
    <div class="post-type"><svg width="12" height="12"><circle cx="3.5" cy="3.5" r="2.3" fill="none" stroke="#666" stroke-width="1.4"/><circle cx="8.5" cy="8.5" r="2.3" fill="none" stroke="#666" stroke-width="1.4"/><line x1="5" y1="5" x2="7" y2="7" stroke="#666" stroke-width="1.4"/></svg>Links</div>
  </div>
</section>

<article class="card post" style="top:301px">
  <div class="avatar" role="img" aria-label="Author profile photo"></div>
  <div class="author">Mark Ellison</div><div class="globe"></div>
  <div class="date">December 12, 2013</div>
  <div class="media" role="img" aria-label="Golf ball on a driving range at sunset" style="background:linear-gradient(180deg,#9fb5bd 0%,#d9c79b 45%,#5f7a3a 70%,#3e5a25 100%)"></div>
  <h3>Nemo enim ipsam voluptatem quia voluptas sit aspernatur</h3>
  <p>Lorem ipsum dolor sit amet, consectetur adipiscing elit, sed do eiusmod tempor incididunt ut labore et dolore magna aliqua. Ut enim ad minim veniam, quis nostrud exercitation ullamco laboris nisi ut aliquip ex ea commodo consequat. m</p>
  <div class="actions"><span>LIKE</span><span>COMMENT</span><span>SHARE</span></div>
</article>

<article class="card post" style="top:566px">
  <div class="avatar" role="img" aria-label="Author profile photo"></div>
  <div class="author">Mark Ellison</div><div class="globe"></div>
  <div class="date">December 12, 2013</div>
  <div class="media" role="img" aria-label="Woman running outdoors at sunset" style="background:linear-gradient(90deg,#4a3216 0%,#c07a2c 30%,#f4d9a0 55%,#d9a265 80%,#5c3a1a 100%)"></div>
  <h3>Nemo enim ipsam voluptatem quia voluptas sit aspernatur</h3>
  <p>Lorem ipsum dolor sit amet, consectetur adipiscing elit, sed do eiusmod tempor incididunt ut labore et dolore magna aliqua. Ut enim ad minim veniam, quis nostrud exercitation ullamco laboris nisi ut aliquip ex ea commodo consequat. m</p>
  <div class="actions"><span>LIKE</span><span>COMMENT</span><span>SHARE</span></div>
</article>

<article class="card post" style="top:830px">
  <div class="avatar" role="img" aria-label="Author profile photo"></div>
  <div class="author">Mark Ellison</div><div class="globe"></div>
  <div class="date">December 12, 2013</div>
  <div class="media" role="img" aria-label="Child wearing a hat" style="background:linear-gradient(90deg,#2b2418 0%,#8c7a52 35%,#5a4a36 65%,#1e1a14 100%)"></div>
  <h3>Nemo enim ipsam voluptatem quia voluptas sit aspernatur</h3>
  <p>Lorem ipsum dolor sit amet, consectetur adipiscing elit, sed do eiusmod tempor incididunt ut labore et dolore magna aliqua. Ut enim ad minim veniam, quis nostrud exercitation ullamco laboris nisi ut aliquip ex ea commodo consequat. m</p>
  <div class="actions"><span>LIKE</span><span>COMMENT</span><span>SHARE</span></div>
</article>

<aside class="card widget" style="top:61px">
  <div class="widget-head">RECENT EVENTS</div>
  <div class="item"><div class="thumb" role="img" aria-label="Event audience" style="background:linear-gradient(135deg,#8a5a3c,#3a2a22)"></div><div class="txt">Lorem ipsum dolor sit amet, consectetur adipiscing elit, sed do</div><div class="meta"><span>NOV 12</span><span class="stars">★★★<i>★★</i></span></div></div>
  <div class="item"><div class="thumb" role="img" aria-label="Conference attendees" style="background:linear-gradient(135deg,#c9d3dc,#4a5a6a)"></div><div class="txt">Lorem ipsum dolor sit amet, consectetur adipiscing elit, sed do</div><div class="meta"><span>NOV 12</span><span class="stars">★★★<i>★★</i></span></div></div>
  <div class="item"><div class="thumb" role="img" aria-label="Speaker at a podium" style="background:linear-gradient(135deg,#d8c9b0,#3a2e26)"></div><div class="txt">Lorem ipsum dolor sit amet, consectetur adipiscing elit, sed do</div><div class="meta"><span>NOV 12</span><span class="stars">★★★<i>★★</i></span></div></div>
</aside>

<aside class="card widget" style="top:281px">
  <div class="widget-head">RECENT BOS</div>
  <div class="item"><div class="person" role="img" aria-label="Member photo" style="background:linear-gradient(135deg,#e9e2da,#8c6e5a)"></div><div class="txt">Lorem ipsum dolor sit amet, consectetur adipiscing elit, sed do</div><div class="meta"><span>RITA LANE</span><span class="stars">★★★<i>★★</i></span></div></div>
  <div class="item"><div class="person" role="img" aria-label="Member photo" style="background:linear-gradient(135deg,#d6d9dd,#2a2e38)"></div><div class="txt">Lorem ipsum dolor sit amet, consectetur adipiscing elit, sed do</div><div class="meta"><span>RITA LANE</span><span class="stars">★★★<i>★★</i></span></div></div>
  <div class="item"><div class="person" role="img" aria-label="Member photo" style="background:linear-gradient(135deg,#e6ddd2,#7a5a46)"></div><div class="txt">Lorem ipsum dolor sit amet, consectetur adipiscing elit, sed do</div><div class="meta"><span>RITA LANE</span><span class="stars">★★★<i>★★</i></span></div></div>
</aside>

<aside class="card widget" style="top:512px;height:200px">
  <div class="widget-head">USER PICKER</div>
  <div class="grid">
    <div role="img" aria-label="Concert crowd" style="background:linear-gradient(#b06a3a,#2a1a14)"></div>
    <div role="img" aria-label="Person walking on a road" style="background:linear-gradient(#c8c8c0,#6a6a50)"></div>
    <div role="img" aria-label="Woman with headphones" style="background:linear-gradient(#3a4a2a,#c9a48a)"></div>
    <div role="img" aria-label="People in a park" style="background:linear-gradient(#6aa03a,#c9b08a)"></div>
    <div role="img" aria-label="Couple looking at a phone" style="background:linear-gradient(#e0d8d0,#7a9ab0)"></div>
    <div role="img" aria-label="Band on stage" style="background:linear-gradient(#2a2a6a,#a0306a)"></div>
    <div role="img" aria-label="Party crowd" style="background:linear-gradient(#3a5ab0,#c03a4a)"></div>
    <div role="img" aria-label="Girl portrait" style="background:linear-gradient(#4a2a1a,#c08a6a)"></div>
    <div role="img" aria-label="Smiling woman outdoors" style="background:linear-gradient(#7aa04a,#d8c07a)"></div>
  </div>
</aside>

<div class="socials">
  <div class="social fb"><i></i>68,876<br>Fans</div>
  <div class="social tw"><i></i>65<br>Followers</div>
  <div class="social gp"><i></i>8,961<br>Followers</div>
</div>

<footer class="footer">
  <div class="footer-icons"><span></span><span></span><span></span><span></span><span></span></div>
  <nav>Home<b>/</b>Contact<b>/</b>Topics<b>/</b>Posts and Comments<b>/</b>Discussion<b>/</b>Videos Links</nav>
  <div class="copyright">Copyright @ 2015 - 2015.Teamora. All Rights Reserved.</div>
</footer>
</body>
</html>
```